Business Card Design - Photographer

I am a landscape photographer and I require a business card design. 

I require two designs:
1)  a double sided business card
 and
b)  a single sided business card 

The single sided design can either be the same as the double sided (with just one side having all the information)....or it can be an entire new design. Its up to you.

My corporate colours are (CMYK):

Blue   69, 32, 0, 0
Grey  72,  64,  47,  31
Green  32,  2,  91,  0
Yellow   0, 19, 92, 0
Orange  0, 39, 75, 0

Colour space in final file should be in CMYK.

The details that need to be included on the card:

- Use the provided Logo
- Name: Wiktor Baranowski
- Email:   sales@vistalumeworks.com.au
- Website:    vistalumeworks.com.au
- Twitter:    twitter.com/vistalumeworks
- Facebook:   facebook.com/vistalumeworks
- Mobile  0417 539 662

Please use the attached template to design the logo to the specified size, including the marked bleed lines. I have also attached my logo in PNG (transparent background) and ai format for you to use.

The final file should be:
- Photoshop version with layers so I can edit the name/text etc. All non vector files should be high resolution at 1039 x 697 pixels at 300 dpi.

I also require a file as:
- Vector based PDF

Anyway questions please contact me.

Thank you

Industry/Entity Type

Landscape

Logo styles of interest
Pictorial/Combination Logo
Abstract Logo
Wordmark Logo
Lettermark Logo
Requirements
Must have
• The details that need to be included on the card:

- Use the provided Logo
- Name: Wiktor Baranowski
- Email: sales@vistalumeworks.com.au
- Website: vistalumeworks.com.au
- Twitter: twitter.com/vistalumeworks
- Facebook: facebook.com/vistalumeworks
- Mobile 0417 539 662

```html
<!DOCTYPE html>
<html lang="en">
<head>
<meta charset="utf-8">
<title>Vistalume Works – Business Card</title>
<link rel="stylesheet" href="https://fonts.googleapis.com/css2?family=Cinzel:wght@400;600&family=Source+Sans+3:wght@400;600&display=swap">
<style>
  :root {
    --stage: #e9e4d8;
    --card: #ffffff;
    --card-shade: #f1f1f1;
    --ink: #3d3f52;
    --text: #222222;
    --orange: #f9a94a;
    --yellow: #fcc916;
    --green: #b7d33a;
    --teal: #6fae9a;
    --blue: #3b8fd4;
    --icon-blue: #3b8fd4;
    --icon-navy: #3b5a98;
  }
  html, body {
    margin: 0;
    padding: 0;
    width: 1200px;
    height: 686px;
    overflow: hidden;
    background: var(--stage);
  }
  .canvas {
    position: relative;
    width: 1200px;
    height: 686px;
    font-family: "Source Sans 3", "Myriad Pro", sans-serif;
    color: var(--text);
  }
  .card {
    position: absolute;
    width: 524px;
    height: 299px;
    background: radial-gradient(ellipse at 55% 20%, var(--card) 40%, var(--card-shade) 100%);
    box-shadow: 1px 2px 3px rgba(0,0,0,0.25);
    overflow: hidden;
  }
  .card--front { left: 60px; top: 147px; }
  .card--back { left: 621px; top: 244px; background: var(--card); }

  .brand-lockup {
    position: absolute;
    left: 28px;
    top: 62px;
    width: 250px;
    text-align: center;
  }
  .brand-dot {
    display: block;
    width: 74px;
    height: 74px;
    margin: 0 auto 12px;
    border-radius: 50%;
    background: var(--ink);
  }
  .brand-name {
    font-family: "Cinzel", "Trajan Pro", serif;
    font-weight: 400;
    font-size: 22px;
    letter-spacing: 0.5px;
    color: var(--ink);
    margin: 0;
    line-height: 1.1;
    border-bottom: 1.5px solid var(--ink);
    padding-bottom: 3px;
  }
  .brand-tagline {
    font-family: "Cinzel", "Trajan Pro", serif;
    font-weight: 600;
    font-size: 9.5px;
    letter-spacing: 1.8px;
    color: var(--ink);
    margin: 5px 0 0;
  }

  .divider {
    position: absolute;
    left: 277px;
    top: 72px;
    width: 1px;
    height: 128px;
    background: var(--ink);
    opacity: 0.8;
  }

  .contact {
    position: absolute;
    left: 302px;
    top: 46px;
    font-size: 12.5px;
    line-height: 1;
    color: var(--text);
  }
  .contact-name {
    margin: 0 0 6px;
    font-size: 14px;
    font-weight: 600;
    color: var(--ink);
    line-height: 18px;
  }
  .contact-row {
    display: flex;
    align-items: center;
    gap: 5px;
    height: 18px;
  }
  .contact-row--gap { margin-top: 12px; }
  .contact-row svg { flex: none; }
  .social-square {
    display: inline-block;
    width: 14px;
    height: 14px;
    border-radius: 2px;
    background: var(--icon-blue);
  }
  .social-square--dark { background: var(--icon-navy); }
  .address {
    margin-top: 12px;
    font-size: 12.5px;
    line-height: 16px;
  }

  .colour-band {
    position: absolute;
    left: 0;
    width: 100%;
    background: linear-gradient(90deg, var(--orange) 0%, var(--yellow) 25%, var(--green) 65%, var(--blue) 100%);
  }
  .card--front .colour-band {
    bottom: 0;
    height: 51px;
    display: flex;
    align-items: center;
    justify-content: center;
  }
  .band-url {
    font-size: 13px;
    color: var(--ink);
    margin-right: 80px;
  }

  .back-url {
    position: absolute;
    top: 0;
    left: 0;
    width: 100%;
    height: 52px;
    display: flex;
    align-items: center;
    justify-content: center;
    font-size: 14px;
    color: var(--ink);
  }
  .card--back .colour-band {
    top: 52px;
    bottom: 0;
    background:
      radial-gradient(ellipse at 20% 20%, rgba(252,201,22,0.9) 0%, rgba(252,201,22,0) 45%),
      linear-gradient(110deg, var(--orange) 0%, var(--yellow) 22%, var(--green) 55%, var(--teal) 78%, var(--blue) 100%);
  }
  .back-mark {
    position: absolute;
    inset: 0;
    display: flex;
    align-items: center;
    justify-content: center;
    gap: 14px;
  }
  .back-mark .brand-dot {
    width: 46px;
    height: 46px;
    margin: 0;
  }
  .back-mark .brand-name {
    border: 0;
    padding: 0;
    font-size: 30px;
  }
</style>
</head>
<body>
<main class="canvas">

  <section class="card card--front" aria-label="Business card front">
    <div class="brand-lockup">
      <span class="brand-dot" aria-hidden="true"></span>
      <p class="brand-name">Vistalume Works</p>
      <p class="brand-tagline">Fine Art Photography</p>
    </div>

    <div class="divider" aria-hidden="true"></div>

    <div class="contact">
      <p class="contact-name">Wiktor Baranowski</p>
      <div class="contact-row">
        <svg width="12" height="13" viewBox="0 0 12 13" aria-hidden="true">
          <path d="M2.5 0.8 L4.6 3.6 L3.4 5 C4 6.8 5.3 8.2 7 9 L8.4 7.7 L11.2 9.7 L10 12 C5 11.6 0.6 7 0.5 2 Z" fill="var(--icon-blue)"/>
        </svg>
        <span>0417 539 662</span>
      </div>
      <div class="contact-row">
        <svg width="13" height="9" viewBox="0 0 13 9" aria-hidden="true">
          <rect x="0" y="0" width="13" height="9" rx="1" fill="var(--icon-blue)"/>
          <path d="M0.5 0.8 L6.5 5 L12.5 0.8" fill="none" stroke="#fff" stroke-width="1"/>
        </svg>
        <span>sales@vistalumeworks.com.au</span>
      </div>
      <div class="contact-row contact-row--gap">
        <span class="social-square" aria-hidden="true"></span>
        <span>@vistalumeworks</span>
      </div>
      <div class="contact-row">
        <span class="social-square social-square--dark" aria-hidden="true"></span>
        <span>@vistalumeworks</span>
      </div>
      <div class="address">Street name City<br>State, zip code</div>
    </div>

    <div class="colour-band">
      <span class="band-url">www.vistalumeworks.com.au</span>
    </div>
  </section>

  <section class="card card--back" aria-label="Business card back">
    <div class="back-url">www.vistalumeworks.com.au</div>
    <div class="colour-band">
      <div class="back-mark">
        <span class="brand-dot" aria-hidden="true"></span>
        <p class="brand-name">Vistalume Works</p>
      </div>
    </div>
  </section>

</main>
</body>
</html>
```